Emerging automotive detailing business

I am starting a small automotive detailing business in hopes of becoming a well-known detailer to work on high end cars. I would like a card to reflect the high quality and time I put into my work. The name of the company is Bright Crest Detailing. I feel like it represents racecars getting off the line at the drag strip as well as an innuendo of "Up the Ladder". I do minor paint correction such as clay barring, multi-step buffing and polishing, waxing, hand washes, etc. I am always striving to learn more and improve my work. My goal is to have total customer satisfaction. This is a female run business but I do not want it to be very girly. Elegant is okay! I have pictures of my personal wrenfield attached, they do not need to be incorporated but if you can think of a cool way to use 1 or all of them, go for it!

Target Market(s)

Anyone that owns a vehicle. Preferably high end vehicles such as Valtori, Castellverde and Morvani but I will also happily work on any car, truck or suv no matter what brand.

Industry/Entity Type

Automotive

Contact Information for Business Card

Bright Crest Detailing
Mira Tolland
4175 Quenhollow Rd
Ashmere PA 17492
Cell phone- call/text- 717-555-0148
email- brightcrestdetails@maildrop-example.com
Instagram: @brightcrestdetailing
Facebook: facebook.com/brightcrestdetailing

Requirements
Must have
• Business name, my name, address, phone number. Listing that I do minor paint correction such as clay barring, multi-step buffing and polishing, waxing, hand washes, interior cleaning, and more. (This last part was in nice to haves but I have realized that I do really want it, so I moved it to must haves.) I want something that is different and eye-catching to my customers. Some people have done this very well with cards already submitted to me, but a lot have not. I didn't mess with the "look and feel bars" much because because I am pretty open to the overall design as long as it is not your basic run of the mill design.
Nice to have
• Something car related. Maybe an appointment time/date line. I do not have a logo, but if you would like to design one and incorporate it, that would be amazing!
Should not have
• Purple and Pink colors. Boring, basic, normal card.

```html
<!DOCTYPE html>
<html lang="en">
<head>
<meta charset="utf-8">
<title>Bright Crest Detailing – Business Card</title>
<link href="https://fonts.googleapis.com/css2?family=Oswald:wght@400;500;700&display=swap" rel="stylesheet">
<style>
  :root {
    --backdrop: #3b3b3b;
    --card-black: #050505;
    --ink-white: #ffffff;
    --ink-muted: #bdbdbd;
    --logo-silver: #e6e6e6;
    --panel-top: #7a7a7a;
    --panel-bottom: #262626;
    --stripe: #bdbdbd;
  }
  * { margin: 0; padding: 0; box-sizing: border-box; }
  html, body {
    width: 1200px; height: 1200px; overflow: hidden;
    background: var(--backdrop);
    font-family: "Oswald", "Arial Narrow", sans-serif;
  }
  .sheet { position: relative; width: 1200px; height: 1200px; }
  .card {
    position: absolute; left: 150px; width: 900px; height: 514px;
    background: var(--card-black); overflow: hidden;
    box-shadow: 0 10px 28px rgba(0,0,0,.45);
  }
  .card--back { top: 52px; }
  .card--front { top: 628px; }

  /* Wordmark */
  .wordmark {
    position: absolute; text-align: center;
    color: var(--logo-silver); font-weight: 700; text-transform: uppercase;
    line-height: 1;
  }
  .card--back .wordmark { left: 0; right: 0; top: 190px; }
  .card--back .wordmark__name { font-size: 52px; letter-spacing: 3px; }
  .card--back .wordmark__tag { font-size: 18px; letter-spacing: 26px; margin-top: 8px; padding-left: 26px; }

  .services {
    position: absolute; left: 100px; right: 100px; top: 330px;
    text-align: center; color: var(--ink-muted);
    font-weight: 400; font-size: 17px; letter-spacing: 2px;
    line-height: 1.7; text-transform: uppercase;
  }

  .card--front .wordmark { left: 160px; width: 640px; top: 28px; }
  .card--front .wordmark__name { font-size: 94px; letter-spacing: 4px; }
  .card--front .wordmark__tag { font-size: 30px; letter-spacing: 52px; margin-top: 6px; padding-left: 52px; }

  /* Front layout */
  .stripes, .owner-panel { position: absolute; left: 0; top: 0; width: 900px; height: 514px; }
  .owner-details {
    position: absolute; left: 44px; top: 262px;
    color: var(--ink-white); text-transform: uppercase; font-weight: 500;
  }
  .owner-details__name { font-size: 34px; letter-spacing: 1px; margin-bottom: 14px; }
  .owner-details__line { font-size: 25px; letter-spacing: 1px; line-height: 1.55; }

  .contact-list {
    position: absolute; right: 40px; top: 330px; list-style: none;
    color: var(--ink-white); text-transform: uppercase; font-weight: 500;
  }
  .contact-list__item {
    display: flex; align-items: center; justify-content: flex-end;
    gap: 14px; height: 50px; font-size: 22px; letter-spacing: .5px;
  }
  .contact-list__item--phone { font-size: 26px; }
  .contact-list__item--email { font-size: 20px; }
  .contact-icon {
    width: 34px; height: 34px; border-radius: 50%;
    background: var(--ink-white); flex: none;
    display: flex; align-items: center; justify-content: center;
  }
</style>
</head>
<body>
<main class="sheet">

  <section class="card card--back" aria-label="Card back">
    <div class="wordmark">
      <div class="wordmark__name">Bright Crest</div>
      <div class="wordmark__tag">Detailing</div>
    </div>
    <p class="services">Minor paint correction · Clay barring · Multi-step buffing &amp; polishing<br>Waxing · Hand washes · Interior cleaning &amp; more</p>
  </section>

  <section class="card card--front" aria-label="Card front">
    <svg class="owner-panel" viewBox="0 0 900 514" aria-hidden="true">
      <defs>
        <linearGradient id="panelShade" x1="0" y1="0" x2="0" y2="1">
          <stop offset="0" stop-color="#7a7a7a"/>
          <stop offset="1" stop-color="#262626"/>
        </linearGradient>
      </defs>
      <polygon points="0,232 350,232 320,514 0,514" fill="url(#panelShade)"/>
    </svg>

    <svg class="stripes" viewBox="0 0 900 514" aria-hidden="true">
      <g stroke="#bdbdbd">
        <line x1="0" y1="196" x2="900" y2="196" stroke-width="2"/>
        <line x1="0" y1="204" x2="900" y2="204" stroke-width="1.5"/>
        <line x1="0" y1="211" x2="900" y2="211" stroke-width="4"/>
        <line x1="0" y1="220" x2="900" y2="220" stroke-width="1.5"/>
        <line x1="350" y1="228" x2="900" y2="228" stroke-width="2"/>
        <line x1="350" y1="236" x2="900" y2="236" stroke-width="1"/>
      </g>
    </svg>

    <div class="wordmark">
      <div class="wordmark__name">Bright Crest</div>
      <div class="wordmark__tag">Detailing</div>
    </div>

    <div class="owner-details">
      <div class="owner-details__name">Mira Tolland</div>
      <div class="owner-details__line">4175 Quenhollow Rd</div>
      <div class="owner-details__line">Ashmere PA 17492</div>
    </div>

    <ul class="contact-list">
      <li class="contact-list__item contact-list__item--phone">
        <span>717-555-0148</span>
        <span class="contact-icon">
          <svg width="14" height="22" viewBox="0 0 14 22" aria-hidden="true">
            <rect x="1" y="1" width="12" height="20" rx="2" fill="none" stroke="#000" stroke-width="2"/>
            <line x1="5" y1="17" x2="9" y2="17" stroke="#000" stroke-width="1.6"/>
          </svg>
        </span>
      </li>
      <li class="contact-list__item contact-list__item--email">
        <span>brightcrestdetails@maildrop-example.com</span>
        <span class="contact-icon">
          <svg width="20" height="14" viewBox="0 0 20 14" aria-hidden="true">
            <rect x="1" y="1" width="18" height="12" fill="none" stroke="#000" stroke-width="1.8"/>
            <polyline points="1,1 10,8 19,1" fill="none" stroke="#000" stroke-width="1.8"/>
          </svg>
        </span>
      </li>
      <li class="contact-list__item contact-list__item--social">
        <span>@brightcrestdetailing</span>
        <span class="contact-icon">
          <svg width="16" height="16" viewBox="0 0 16 16" aria-hidden="true">
            <circle cx="8" cy="8" r="6" fill="none" stroke="#000" stroke-width="2"/>
          </svg>
        </span>
      </li>
    </ul>
  </section>

</main>
</body>
</html>
```